Venture Capital Investment Firm

We are looking to overhaul our existing website (substantially), with only using the same logos (which we can provide).
We are an investment firm that focuses on making loans to late stage technology companies. Our site should ultimately look like other venture capital firms, and look modern and fresh. We have an existing website www.norvellhub.com which this will be replacing, although we will be using a lot of the existing written content, and potentially the numbers of pages we will need, we are not wed to anything else. Please feel free to shoot any questions at any time and thank you in advance for your help!
Websites we like as examples:
https://www.tesmarkfund.com/
https://www.brindlewoodpartners.com/
Target Market(s)
Potential investors who will invest in our firm, as well as potentially companies that are looking to borrow money from us.
Coding
Coded - Design and coding required
Number of Pages Required
5+ page
Colors
Designer to choose colors to be used in the design.
Look and feel

```html
<!DOCTYPE html>
<html lang="en">
<head>
<meta charset="utf-8">
<title>Norvell Hub — Structured Credit Investment</title>
<link rel="stylesheet" href="https://fonts.googleapis.com/css2?family=Lora:wght@400;700&family=Open+Sans:wght@400;600&display=swap">
<style>
:root{
  --navy:#0e0c3d;
  --ink:#222233;
  --grey:#555566;
  --lavender:#dcdaf8;
  --lavender-soft:#ebeafc;
  --white:#ffffff;
  --line:#cfcfdc;
}
*{box-sizing:border-box;margin:0;padding:0}
html,body{width:1200px;height:3072px;overflow:hidden;background:var(--white)}
body{position:relative;font-family:"Open Sans",sans-serif;color:var(--ink)}
.abs{position:absolute}
.serif{font-family:"Lora",serif}

/* header */
.site-header{left:0;top:0;width:1200px;height:88px;background:var(--white)}
.brand{left:144px;top:18px;display:flex;align-items:center;gap:12px}
.brand-mark{width:38px;height:38px;border-radius:50%;background:var(--navy)}
.brand-name{font-family:"Lora",serif;font-size:30px;color:var(--navy);line-height:1}
.brand-sub{font-family:"Lora",serif;font-size:9px;color:var(--navy);letter-spacing:.5px;margin-top:4px}
.login{left:923px;top:16px;width:132px;height:29px;border:1px solid #bbb;font-size:11px;color:#444;display:flex;align-items:center;justify-content:center;gap:8px}
.nav{right:145px;top:57px;display:flex;gap:33px;font-family:"Lora",serif;font-size:13px;color:#666}
.nav .current{color:var(--navy)}

/* hero */
.hero{left:0;top:88px;width:1200px;height:568px;background:linear-gradient(120deg,#6f6f78 0%,#9c9ca2 35%,#5a5a64 70%,#2d2d38 100%)}
.hero-copy{left:145px;top:192px;font-family:"Lora",serif;font-weight:700;font-size:21px;line-height:29px;color:var(--white)}
.btn{background:var(--navy);color:var(--white);font-family:"Lora",serif;border-radius:22px;display:flex;align-items:center;justify-content:center}
.hero-btn{left:145px;top:285px;width:160px;height:38px;font-size:16px}
.slide-arrow{width:40px;height:40px;border-radius:50%;background:var(--navy);display:flex;align-items:center;justify-content:center;top:330px}

/* generic headings */
.center{left:0;width:1200px;text-align:center}
.h2{font-family:"Lora",serif;font-weight:700;font-size:33px;color:var(--navy)}
.h3{font-size:24px;color:var(--grey);letter-spacing:.3px}
.h-serif{font-family:"Lora",serif;font-size:34px;color:var(--ink)}
.intro{left:140px;width:920px;top:822px;text-align:center;font-size:15px;line-height:27.5px;color:#555}

.band{left:0;width:1200px;background:var(--lavender)}
.card{background:var(--white);position:absolute}
.focus-list{position:absolute;left:198px;top:22px;list-style:none;font-size:19px;line-height:48px;color:#111}
.focus-list li::before{content:"•";margin-right:12px;font-size:14px;vertical-align:2px}

.ttype{top:1843px;width:300px;height:135px;text-align:center}
.ttype-label{position:absolute;left:0;width:100%;top:92px;font-family:"Lora",serif;font-size:22px;color:var(--ink)}
.ttype svg{position:absolute;left:50%;margin-left:-35px;top:8px}
.divider{top:1843px;width:1px;height:135px;background:var(--line)}

.news-card{top:2231px;width:298px;height:95px;padding:18px 16px;font-family:"Lora",serif}
.news-date{font-size:13px;color:#222}
.news-text{font-size:11px;line-height:18px;color:#444;margin-top:10px;font-family:"Open Sans",sans-serif}

.map{left:0;top:2434px;width:1200px;height:500px;background:linear-gradient(135deg,#eeede9 0%,#e6e4de 45%,#efe6b8 55%,#e8e7e2 100%)}
.contact-bar{left:144px;top:2481px;width:911px;height:46px;background:var(--white);display:flex;align-items:center;justify-content:space-between;padding:0 28px 0 22px;font-size:16px;color:#111}
.contact-bar span{display:flex;align-items:center;gap:8px}

.footer{left:0;top:2935px;width:1200px;height:137px;background:var(--navy)}
.footer-links{left:145px;top:2985px;font-size:12px;color:#cfcfe6}
.footer-links b{font-weight:400;margin:0 9px}
.copyright{left:145px;top:3020px;font-size:12px;color:#cfcfe6}
.social{top:3002px;width:16px;height:16px;border-radius:50%;background:#9a99b8}
</style>
</head>
<body>

<header class="abs site-header">
  <div class="abs brand">
    <div class="brand-mark"></div>
    <div>
      <div class="brand-name">Norvell Hub</div>
      <div class="brand-sub">INVESTMENT PARTNERS, LLC</div>
    </div>
  </div>
  <div class="abs login">
    <svg width="12" height="12" viewBox="0 0 12 12"><path d="M1 6h7M5 3l3 3-3 3M8 1h3v10H8" fill="none" stroke="#333" stroke-width="1.4"/></svg>
    INVESTOR LOGIN
  </div>
  <nav class="abs nav">
    <span class="current">HOME</span><span>STRATEGY</span><span>ABOUT US</span><span>TEAM</span><span>NEWS</span><span>CONTACT</span>
  </nav>
</header>

<section class="abs hero" role="img" aria-label="Photo of hands using a tablet over a desk with charts, a laptop and a pen"></section>
<div class="abs hero-copy">WE ARE A GLOBAL STRUCTURED<br>CREDIT INVESTMENT FIRM FOCUSED ON THE<br>HEALTHCARE AND TECHNOLOGY INDUSTRIES</div>
<div class="abs btn hero-btn">OUR STRATEGY</div>
<div class="abs slide-arrow" style="left:55px"><svg width="14" height="14" viewBox="0 0 14 14"><path d="M9 2L4 7l5 5" fill="none" stroke="#fff" stroke-width="2.4"/></svg></div>
<div class="abs slide-arrow" style="left:1103px"><svg width="14" height="14" viewBox="0 0 14 14"><path d="M5 2l5 5-5 5" fill="none" stroke="#fff" stroke-width="2.4"/></svg></div>

<!-- hero bottom wave -->
<svg class="abs" style="left:0;top:610px" width="1200" height="50" viewBox="0 0 1200 50" preserveAspectRatio="none">
  <path d="M0 40 C120 0 200 10 300 30 C420 55 480 0 600 15 C700 28 760 45 880 20 C990 0 1060 5 1200 30 V50 H0Z" fill="var(--lavender)"/>
  <path d="M0 50 C150 30 250 40 360 48 C480 30 560 30 640 45 C760 35 860 30 980 45 C1080 35 1150 40 1200 44 V50 H0Z" fill="var(--white)"/>
</svg>

<h2 class="abs center h2" style="top:730px">NORVELL HUB STARTED WITH A BIG IDEA:</h2>
<div class="abs center h3" style="top:782px">FINANCE PROVEN INNOVATION WITH A DIFFERENT APPROACH</div>
<p class="abs intro">Norvell Hub is a private investment firm unique in its dual focus on life science and technology credit opportunities. Our ambidextrous approach to investing reflects a broad recognition and appreciation for the critical role intellectual property plays in the successful commercialization of products. We apply our extensive industry expertise to assess the revenue visibility created by these assets and offer a range of creative financing solutions.</p>

<!-- partners band -->
<svg class="abs" style="left:0;top:995px" width="1200" height="60" viewBox="0 0 1200 60" preserveAspectRatio="none">
  <path d="M0 20 C120 40 200 45 320 25 C440 5 520 40 640 30 C760 20 860 5 980 25 C1080 40 1150 30 1200 15 V60 H0Z" fill="var(--lavender-soft)"/>
  <path d="M0 40 C100 25 180 5 300 20 C420 35 500 50 620 30 C740 15 820 5 940 25 C1060 45 1140 40 1200 30 V60 H0Z" fill="var(--lavender)"/>
</svg>
<section class="abs band" style="top:1054px;height:620px"></section>
<svg class="abs" style="left:0;top:1672px" width="1200" height="40" viewBox="0 0 1200 40" preserveAspectRatio="none">
  <path d="M0 0 H1200 V20 C1100 35 1000 25 900 15 C780 5 700 30 600 30 C500 30 420 10 300 15 C180 20 80 40 0 25Z" fill="var(--lavender)"/>
</svg>

<h2 class="abs center h2" style="top:1119px">PARTNERS FOR GROWTH</h2>
<div class="abs center h3" style="top:1170px;line-height:29px">WE PROVIDE FLEXIBLE CAPITAL TO INNOVATIVE COMPANIES AND<br>THEIR INVESTORS</div>
<div class="abs center h-serif" style="top:1253px">Industry Focus</div>

<div class="card" style="left:144px;top:1327px;width:432px;height:176px">
  <svg class="abs" style="left:40px;top:38px" width="104" height="104" viewBox="0 0 104 104" fill="none" stroke="#555" stroke-width="2.5">
    <path d="M8 4 C40 30 -4 60 30 100 M34 4 C4 30 46 60 8 100"/>
    <path d="M12 22h18M10 40h18M12 62h18M10 82h20"/>
    <rect x="52" y="14" width="14" height="40" rx="3" transform="rotate(35 59 34)"/>
    <path d="M60 70 a22 22 0 0 0 30 -28 M44 96h56v-10H44z M70 86v-16"/>
  </svg>
  <ul class="focus-list"><li>Biopharma</li><li>Devices</li><li>Tools &amp; Diagnostics</li></ul>
</div>
<div class="card" style="left:623px;top:1327px;width:432px;height:176px">
  <svg class="abs" style="left:40px;top:38px" width="108" height="104" viewBox="0 0 108 104" fill="none" stroke="#555" stroke-width="2.5">
    <rect x="4" y="4" width="92" height="62" rx="4"/>
    <path d="M4 54h92M40 66v10h-12M24 22l-8 8 8 8M42 40l10-20M60 22l8 8-8 8M72 36h2M78 36h2"/>
    <circle cx="84" cy="84" r="12"/><circle cx="84" cy="84" r="5"/>
    <path d="M6 96a10 10 0 0 1 20 0z"/>
  </svg>
  <ul class="focus-list"><li>Software &amp; Services</li><li>Hardware</li><li>Systems</li></ul>
</div>
<div class="abs btn" style="left:528px;top:1545px;width:144px;height:39px;font-size:16px">READ MORE</div>

<!-- transaction types -->
<div class="abs center h-serif" style="top:1776px">Transaction Types</div>
<div class="abs ttype" style="left:136px">
  <svg width="70" height="70" viewBox="0 0 70 70" fill="none" stroke="#555" stroke-width="2.5">
    <rect x="22" y="4" width="26" height="18" rx="2"/><path d="M28 10h14M28 15h10M35 22v10M12 32h46M12 32v8M35 32v8M58 32v8"/>
    <rect x="3" y="40" width="18" height="22"/><rect x="26" y="40" width="18" height="22"/><rect x="49" y="40" width="18" height="22"/>
  </svg>
  <div class="ttype-label">Structured Credit</div>
</div>
<div class="abs divider" style="left:429px"></div>
<div class="abs ttype" style="left:450px">
  <svg width="70" height="70" viewBox="0 0 70 70" fill="none" stroke="#555" stroke-width="2.5">
    <circle cx="35" cy="35" r="28" stroke-dasharray="60 8"/><circle cx="35" cy="35" r="18"/>
    <path d="M41 28c-2-3-12-3-12 2s12 4 12 9-10 5-12 2M35 20v30"/>
  </svg>
  <div class="ttype-label">Milestones &amp; Royalties</div>
</div>
<div class="abs divider" style="left:781px"></div>
<div class="abs ttype" style="left:763px">
  <svg width="70" height="70" viewBox="0 0 70 70" fill="none" stroke="#555" stroke-width="2.5">
    <rect x="20" y="4" width="30" height="62"/><rect x="4" y="24" width="16" height="42"/><rect x="50" y="18" width="16" height="48"/>
    <path d="M27 12h4M39 12h4M27 24h4M39 24h4M27 36h4M39 36h4M30 66v-14h10v14M9 34h6M9 46h6M55 30h6M55 44h6"/>
  </svg>
  <div class="ttype-label">Legacy Assets</div>
</div>

<!-- news band -->
<svg class="abs" style="left:0;top:2050px" width="1200" height="60" viewBox="0 0 1200 60" preserveAspectRatio="none">
  <path d="M0 30 C120 5 220 10 340 30 C460 50 540 10 660 15 C780 20 860 45 980 30 C1080 18 1150 10 1200 20 V60 H0Z" fill="var(--lavender-soft)"/>
  <path d="M0 45 C150 10 250 5 380 30 C500 50 560 20 680 25 C800 30 880 10 1000 20 C1100 30 1160 35 1200 30 V60 H0Z" fill="var(--lavender)"/>
</svg>
<section class="abs band" style="top:2108px;height:340px"></section>

<h2 class="abs center h2" style="top:2175px">NEWS</h2>
<svg class="abs" style="left:56px;top:2264px" width="16" height="28" viewBox="0 0 16 28"><path d="M13 2L3 14l10 12" fill="none" stroke="#666" stroke-width="2.5"/></svg>
<svg class="abs" style="left:1128px;top:2264px" width="16" height="28" viewBox="0 0 16 28"><path d="M3 2l10 12L3 26" fill="none" stroke="#666" stroke-width="2.5"/></svg>
<div class="card news-card" style="left:144px">
  <div class="news-date">April 2018</div>
  <div class="news-text">Norvell Hub completes structured debt investment<br>in Tallowleaf</div>
</div>
<div class="card news-card" style="left:451px">
  <div class="news-date">Oct. 2016</div>
  <div class="news-text">Norvell Hub completes $22,000,000 structured debt<br>investment in Pinecrest Labs</div>
</div>
<div class="card news-card" style="left:758px">
  <div class="news-date">April 2016</div>
  <div class="news-text">Orrin Microsystems acquired by Veltane for<br>$55,000,000</div>
</div>

<!-- map -->
<section class="abs map" role="img" aria-label="Street map of the office neighbourhood with a pin marking the office location"></section>
<svg class="abs" style="left:0;top:2430px" width="1200" height="30" viewBox="0 0 1200 30" preserveAspectRatio="none">
  <path d="M0 0H1200V8C1100 20 1000 22 880 12C760 2 680 20 560 18C440 16 360 4 240 10C140 15 60 22 0 14Z" fill="var(--lavender)"/>
</svg>
<div class="abs contact-bar">
  <span><svg width="11" height="16" viewBox="0 0 11 16"><path d="M5.5 0a5.5 5.5 0 0 0-5.5 5.5C0 10 5.5 16 5.5 16S11 10 11 5.5A5.5 5.5 0 0 0 5.5 0zm0 8a2.5 2.5 0 1 1 0-5 2.5 2.5 0 0 1 0 5z" fill="#111"/></svg>2400 Larkmoor Avenue #310, Fremont Bay, CA&nbsp; 94020</span>
  <span><svg width="14" height="14" viewBox="0 0 14 14"><path d="M3 1l2.5 3-1.5 2c1 2 2 3 4 4l2-1.5 3 2.5-1.5 2.5C6 13 1 8 .5 2.5z" fill="#111"/></svg>555 30 1847</span>
  <span><svg width="16" height="12" viewBox="0 0 16 12"><rect width="16" height="12" rx="1" fill="#111"/><path d="M1 1l7 6 7-6" fill="none" stroke="#fff" stroke-width="1.4"/></svg>info@norvellhub.com</span>
</div>

<!-- footer -->
<svg class="abs" style="left:0;top:2890px" width="1200" height="48" viewBox="0 0 1200 48" preserveAspectRatio="none">
  <path d="M0 40C100 20 200 10 320 25C440 40 520 40 640 25C760 10 860 20 980 30C1080 38 1150 20 1200 15V48H0Z" fill="var(--navy)"/>
</svg>
<footer class="abs footer"></footer>
<div class="abs footer-links">Home<b>|</b>Strategy<b>|</b>About Us<b>|</b>Team<b>|</b>News<b>|</b>Contact</div>
<div class="abs copyright">Copyright &copy; 2019&nbsp; Norvell Hub.&nbsp; All rights reserved.</div>
<div class="abs social" style="left:994px"></div>
<div class="abs social" style="left:1038px"></div>

</body>
</html>
```